Quorva - corporate Business Card

We need a good look and innovative business card for a new start up company based in Los Angeles called "Quorva". We are in a payment business, including payment card, app, and ewallet. We are expert in online payment and Card not present (CNP) transaction.
We need an innovative, modern business card.

Our logo font is Aero Matics

Target Market(s)

Startup - Bank - Online Payment - Card Manufacturing

Industry/Entity Type

Startup

Contact Information for Business Card

phone: 555 014 7396 - Address: 4172 Marlowe blvd, Ferndale Park, CA 90299

Requirements
Must have
• Message: innovative, professional, expert, high tech, trust, online payment expert, security
Nice to have
• no comment
Should not have
• no Comment

```html
<!DOCTYPE html>
<html lang="en">
<head>
<meta charset="utf-8">
<title>Quorva business card</title>
<link href="https://fonts.googleapis.com/css2?family=Open+Sans:wght@400;500;600;700&display=swap" rel="stylesheet">
<style>
  :root {
    --backdrop: #ebe7e2;
    --brand-red: #b71f2e;
    --paper: #ffffff;
    --divider: #9a9a9a;
    --ink-light: #ffffff;
  }
  * { margin: 0; padding: 0; box-sizing: border-box; }
  html, body {
    width: 1200px;
    height: 987px;
    overflow: hidden;
    background: var(--backdrop);
    font-family: "Open Sans", Arial, sans-serif;
  }
  .canvas {
    position: relative;
    width: 1200px;
    height: 987px;
  }
  .card {
    position: absolute;
    left: 293px;
    width: 615px;
    height: 351px;
    box-shadow: 0 2px 6px rgba(0,0,0,0.25);
  }
  .card-front { top: 130px; display: flex; background: var(--brand-red); }
  .card-back { top: 506px; background: var(--brand-red); }

  .front-brand {
    position: relative;
    width: 319px;
    height: 100%;
    background: var(--paper);
    border-right: 4px solid var(--divider);
  }
  .brand-lockup {
    position: absolute;
    left: 48px;
    top: 143px;
    display: flex;
    align-items: center;
    gap: 10px;
  }
  .brand-dot {
    width: 68px;
    height: 68px;
    border-radius: 50%;
    background: var(--brand-red);
  }
  .brand-name {
    font-size: 44px;
    font-weight: 500;
    color: var(--brand-red);
    line-height: 1;
    letter-spacing: 0.5px;
    margin-top: -6px;
  }

  .front-details {
    position: relative;
    flex: 1;
    color: var(--ink-light);
  }
  .holder {
    position: absolute;
    left: 41px;
    top: 78px;
  }
  .holder-name {
    font-size: 21px;
    font-weight: 600;
    line-height: 1.2;
  }
  .holder-role {
    font-size: 16px;
    font-weight: 400;
    line-height: 1.3;
  }
  .address {
    position: absolute;
    left: 41px;
    top: 150px;
    font-size: 16px;
    line-height: 23px;
    font-style: normal;
  }
  .contact-list {
    position: absolute;
    left: 41px;
    top: 204px;
    list-style: none;
    font-size: 16px;
    line-height: 23.5px;
  }
  .contact-list li { display: flex; align-items: center; gap: 11px; }
  .contact-icon { width: 15px; height: 15px; flex: none; }

  .back-mark {
    position: absolute;
    left: 213px;
    top: 72px;
    width: 188px;
    height: 188px;
    border-radius: 50%;
    background: var(--paper);
  }
  .back-url {
    position: absolute;
    left: 0;
    right: 0;
    top: 290px;
    text-align: center;
    color: var(--ink-light);
    font-size: 15px;
    letter-spacing: 6px;
  }
</style>
</head>
<body>
<main class="canvas">
  <section class="card card-front">
    <div class="front-brand">
      <div class="brand-lockup">
        <span class="brand-dot"></span>
        <span class="brand-name">quorva</span>
      </div>
    </div>
    <div class="front-details">
      <div class="holder">
        <p class="holder-name">DANIEL REYES</p>
        <p class="holder-role">CEO&amp;Founder</p>
      </div>
      <address class="address">4172 Marlowe blvd<br>Ferndale Park, CA 90299</address>
      <ul class="contact-list">
        <li>
          <svg class="contact-icon" viewBox="0 0 24 24" aria-hidden="true"><path fill="#fff" d="M6.6 10.8c1.4 2.8 3.8 5.1 6.6 6.6l2.2-2.2c.3-.3.7-.4 1-.2 1.1.4 2.3.6 3.6.6.6 0 1 .4 1 1V20c0 .6-.4 1-1 1C10.6 21 3 13.4 3 4c0-.6.4-1 1-1h3.5c.6 0 1 .4 1 1 0 1.3.2 2.5.6 3.6.1.3 0 .7-.2 1L6.6 10.8z"/></svg>
          <span>555 014 7396</span>
        </li>
        <li>
          <svg class="contact-icon" viewBox="0 0 24 24" aria-hidden="true"><rect x="2" y="5" width="20" height="14" fill="#fff"/><path d="M2 5l10 8 10-8" fill="none" stroke="#b71f2e" stroke-width="2"/></svg>
          <span>daniel@quorva.com</span>
        </li>
        <li>
          <svg class="contact-icon" viewBox="0 0 24 24" aria-hidden="true"><circle cx="12" cy="12" r="10" fill="#fff"/><path d="M12 2c-3 3-3 17 0 20M2 12h20M4 7h16M4 17h16" fill="none" stroke="#b71f2e" stroke-width="1.6"/></svg>
          <span>www.quorva.com</span>
        </li>
      </ul>
    </div>
  </section>

  <section class="card card-back">
    <div class="back-mark"></div>
    <p class="back-url">www.quorva.com</p>
  </section>
</main>
</body>
</html>
```